Brightcoat Painting Services Requires a New Responsive Site

Hi Designers,

Our current website is this www.brightcoatpainting.com.au for some idea.
I made it on Adobe Muse, its very basic.
I would like it to be redesigned to look more professional and also responsive. I actually know how to do html5 and css but I think others will do this much better than me.

I do not need content because I am a copywriter and would like to do all SEO and copy myself.

The most improtant things to remember is that the site cannot use a CMS
and the code needs to be understandable so that I can go in and add content later on and do SEO work.

Also the site requires an additional testimonial page. I would imagine a nice gallery would be a great addition too(something that I can add images too through html. Also in it is important for it to contain those brand images on the front page as it increases authority. I will attach them onto the brief.

Those two files of nearbyfind and tradeleafs are local directories where we have reviews so a placement of those on the testimonail page would make great sense. I will to the href myself.

Anyway, good luck!

I look forward to see your designs :D
Updates

I have just been informed that on this site websites are simply designed and not built (developed) if this is the case please stop working on your designs and spending more time on this project. I REQUIRE DEVELOPMENT ALSO AND HAVE ALREADY CONTACTED SUPPORT.

Target Market(s)

The target market is 30-75 high income earners.

Industry/Entity Type

Painting

Number of Pages Required

5+ page

Font styles to use
Serif
Sans Serif

Requirements
Must have
• attractive gallery, and the brand icons uploaded.
• must be responsive
• web carousel (with the different types of work we do). eg domestic, commercial, industrial etc.
Nice to have
• a little interactivity
• corporate a natural design that goes well with our logo
Should not have
• any content. just write jiberish to fill in the spaces.
• I will be doing all copy and SEO myself.
• More than five pages, bascially the four that already exist plus the testimonail one.

```html
<!DOCTYPE html>
<html lang="en">
<head>
<meta charset="utf-8">
<title>Brightcoat Painting Services</title>
<link href="https://fonts.googleapis.com/css2?family=Mulish:wght@300;400;600;700;800&display=swap" rel="stylesheet">
<style>
:root{
  --header-top:#4a4a4a;
  --header-bottom:#232323;
  --accent:#2f8fd6;
  --accent-dark:#1f6fae;
  --band:#4aa3df;
  --band-light:#7cc0ec;
  --text:#555;
  --heading:#444;
  --muted:#8a8a8a;
  --badge:#c9ced6;
  --footer:#2b2b2b;
  --footer-bottom:#1d1d1d;
  --white:#fff;
}
*{box-sizing:border-box;margin:0;padding:0}
html,body{width:669px;height:1200px;overflow:hidden;background:var(--white)}
body{position:relative;font-family:'Mulish',sans-serif;color:var(--text)}
.site-header{position:absolute;left:0;top:0;width:669px;height:82px;background:linear-gradient(var(--header-top),var(--header-bottom))}
.brand{position:absolute;left:96px;top:14px;display:flex;align-items:center;gap:8px}
.brand-mark{width:26px;height:26px;background:var(--accent);border-radius:3px}
.brand-name{color:var(--white);font-weight:700;font-size:15px;line-height:16px;width:90px}
.enquiry{position:absolute;right:92px;top:10px;text-align:right;color:#ddd;font-size:10px;line-height:13px}
.enquiry strong{display:block;color:var(--white);font-size:12px}
.main-nav{position:absolute;right:92px;top:50px;display:flex;gap:2px}
.main-nav a{color:#eee;font-size:9px;font-weight:700;text-decoration:none;padding:7px 9px;text-transform:uppercase}
.main-nav a.active{background:var(--accent);border-radius:2px}
.hero{position:absolute;left:0;top:82px;width:669px;height:270px;background:linear-gradient(100deg,#e8dccd 0%,#c9792e 35%,#d8742a 60%,#b9a58d 100%)}
.hero-caption{position:absolute;left:89px;top:114px;width:202px;padding:10px 12px;background:rgba(30,40,50,.7);color:var(--white)}
.hero-caption h2{font-size:14px;font-weight:600;line-height:16px}
.hero-caption h3{font-size:12px;font-weight:400;color:#9fd2f6;line-height:15px}
.hero-caption p{font-size:7px;line-height:9px;color:#ccc;margin-top:4px}
.hero-dots{position:absolute;left:318px;top:257px;display:flex;gap:4px}
.hero-dots span{width:6px;height:6px;border-radius:50%;background:#ccc}
.hero-dots span.on{background:var(--accent)}
.services{position:absolute;left:88px;top:365px;width:494px;display:flex;justify-content:space-between}
.service{width:112px;text-align:center}
.service-icon{width:54px;height:54px;border-radius:50%;border:1px solid #ddd;margin:0 auto;display:flex;align-items:center;justify-content:center}
.service h4{font-size:11px;font-weight:600;color:var(--heading);margin-top:14px}
.service p{font-size:6.5px;line-height:8px;color:var(--muted);margin-top:4px}
.btn{display:inline-block;margin-top:6px;background:var(--accent-dark);color:var(--white);font-size:6px;font-weight:700;padding:3px 7px;border-radius:2px}
.about{position:absolute;left:96px;top:530px;width:477px;text-align:center}
.about h2{font-size:20px;font-weight:300;color:var(--heading)}
.about p{font-size:6.5px;line-height:9px;color:var(--muted);margin-top:8px}
.gallery{position:absolute;left:0;top:680px;width:669px;height:240px}
.gallery svg.bg{position:absolute;left:0;top:0}
.gallery h2{position:absolute;top:14px;width:669px;text-align:center;color:var(--white);font-size:17px;font-weight:400}
.thumbs{position:absolute;left:100px;top:46px;width:470px;display:grid;grid-template-columns:repeat(5,88px);gap:7px 7px}
.thumb{height:56px;border:2px solid var(--white)}
.partners{position:absolute;left:96px;top:960px;width:477px;display:flex;justify-content:space-between;align-items:center}
.partner{font-size:11px;font-weight:700;color:#3a5a8a;display:flex;align-items:center;gap:4px}
.partner i{display:block;width:12px;height:12px;background:#3a5a8a}
.badge-placeholder{display:block;width:30px;height:30px;background:var(--badge)}
.site-footer{position:absolute;left:0;top:1030px;width:669px;height:170px;background:var(--footer)}
.foot-col{position:absolute;top:16px;color:#bbb;font-size:7.5px;line-height:11px}
.foot-col h5{color:var(--white);font-size:10px;font-weight:700;margin-bottom:4px}
.social{display:flex;gap:4px;margin-top:4px}
.social span{width:10px;height:10px;background:var(--accent)}
.copyright{position:absolute;left:0;bottom:0;width:669px;height:30px;background:var(--footer-bottom);color:#888;font-size:6.5px;padding:11px 96px}
</style>
</head>
<body>
<header class="site-header">
  <div class="brand"><span class="brand-mark"></span><span class="brand-name">Brightcoat Painting</span></div>
  <div class="enquiry">For Enquiry<strong>1300 555 018</strong></div>
  <nav class="main-nav"><a class="active">Home</a><a>About Us</a><a>Services</a><a>Gallery</a><a>Contact Us</a></nav>
</header>

<section class="hero" role="img" aria-label="Photo of a painted living room with an orange feature wall">
  <div class="hero-caption">
    <h2>Curabitur iaculis tempus</h2>
    <h3>Mauris vel lacus vitae felis</h3>
    <p>Donec sed odio dui, nulla vitae elit libero, a pharetra augue mollis interdum.</p>
  </div>
  <div class="hero-dots"><span></span><span class="on"></span><span></span><span></span></div>
</section>

<section class="services">
  <div class="service">
    <div class="service-icon"><svg width="26" height="24" viewBox="0 0 26 24"><path d="M2 12 13 3l11 9" fill="none" stroke="#2f8fd6" stroke-width="2"/><rect x="6" y="11" width="14" height="12" fill="#2f8fd6"/></svg></div>
    <h4>Domestic Painting</h4>
    <p>Lorem ipsum dolor sit amet, consectetur adipiscing elit sed do eiusmod tempor incididunt ut labore.</p>
    <span class="btn">READ MORE</span>
  </div>
  <div class="service">
    <div class="service-icon"><svg width="22" height="26" viewBox="0 0 22 26"><rect x="3" y="2" width="16" height="24" fill="#2f8fd6"/><g fill="#fff"><rect x="6" y="5" width="3" height="3"/><rect x="13" y="5" width="3" height="3"/><rect x="6" y="11" width="3" height="3"/><rect x="13" y="11" width="3" height="3"/><rect x="6" y="17" width="3" height="3"/><rect x="13" y="17" width="3" height="3"/></g></svg></div>
    <h4>Commercial Painting</h4>
    <p>Lorem ipsum dolor sit amet, consectetur adipiscing elit sed do eiusmod tempor incididunt ut labore.</p>
    <span class="btn">READ MORE</span>
  </div>
  <div class="service">
    <div class="service-icon"><svg width="28" height="24" viewBox="0 0 28 24"><path d="M2 23V10l7 5V10l7 5V4h5v19z" fill="#2f8fd6"/></svg></div>
    <h4>Industrial Painting</h4>
    <p>Lorem ipsum dolor sit amet, consectetur adipiscing elit sed do eiusmod tempor incididunt ut labore.</p>
    <span class="btn">READ MORE</span>
  </div>
  <div class="service">
    <div class="service-icon"><svg width="24" height="26" viewBox="0 0 24 26"><path d="M12 1 4 9v16h16V9z" fill="#2f8fd6"/><rect x="10" y="16" width="4" height="9" fill="#fff"/></svg></div>
    <h4>Heritage Painting</h4>
    <p>Lorem ipsum dolor sit amet, consectetur adipiscing elit sed do eiusmod tempor incididunt ut labore.</p>
    <span class="btn">READ MORE</span>
  </div>
</section>

<section class="about">
  <h2>About Our Company</h2>
  <p>Brightcoat Painting is an Australian family owned painting and decorating business based in the south side of Melbourne. We proudly provide domestic and commercial painting services across all suburbs of metropolitan Melbourne.</p>
  <p>Mauris vel lacus vitae felis vestibulum volutpat. Etiam est nunc, venenatis in tristique eu, imperdiet ac nisl. Cum sociis natoque penatibus et magnis dis parturient montes nascetur ridiculus mus. In iaculis facilisis massa. Etiam eu urna. Sed porta ipsum. Vestibulum ante ipsum primis in faucibus orci luctus et ultrices posuere cubilia curae. Aenean et lectus nec ligula pretium ultrices. Donec non nisi, aliquam in, dapibus quis, pretium mauris.</p>
</section>

<section class="gallery">
  <svg class="bg" width="669" height="240" viewBox="0 0 669 240"><path d="M0 0h669v190L334 240 0 190z" fill="#4aa3df"/><path d="M0 150 334 205 669 150v40L334 240 0 190z" fill="#7cc0ec"/></svg>
  <h2>Our Gallery</h2>
  <div class="thumbs">
    <div class="thumb" role="img" aria-label="Painted bedroom" style="background:linear-gradient(#8fb7a0,#c9b08e)"></div>
    <div class="thumb" role="img" aria-label="Painted hallway" style="background:linear-gradient(#e6e2da,#b7a995)"></div>
    <div class="thumb" role="img" aria-label="Painted lounge" style="background:linear-gradient(#c9a98a,#7a5f48)"></div>
    <div class="thumb" role="img" aria-label="Painted dining room" style="background:linear-gradient(#d8d1c6,#9e8c78)"></div>
    <div class="thumb" role="img" aria-label="Painted living room" style="background:linear-gradient(#b9c7cf,#6f7f88)"></div>
    <div class="thumb" role="img" aria-label="Painted kitchen" style="background:linear-gradient(#dcd3c4,#a08a6d)"></div>
    <div class="thumb" role="img" aria-label="Painted study" style="background:linear-gradient(#cfc7b8,#857564)"></div>
    <div class="thumb" role="img" aria-label="Painted staircase" style="background:linear-gradient(#eeeae4,#b3aca2)"></div>
    <div class="thumb" role="img" aria-label="Painted family room" style="background:linear-gradient(#d6cbb6,#8c7b62)"></div>
    <div class="thumb" role="img" aria-label="Painted open plan home" style="background:linear-gradient(#e7e3dc,#a9a196)"></div>
  </div>
</section>

<section class="partners">
  <span class="partner"><i></i>nearbyfind</span>
  <span class="badge-placeholder" role="img" aria-label="Trade association membership badge"></span>
  <span class="partner" style="color:#b0352f">Hartwell</span>
  <span class="partner" style="color:#222">tradeleafs</span>
  <span class="partner" style="color:#c23a2a">Tamberly</span>
  <span class="partner" style="color:#1e3f8a">Colourline</span>
</section>

<footer class="site-footer">
  <div class="foot-col" style="left:96px"><h5>Information</h5>About Us<br>Our Services<br>Our Gallery<br>Contact Us</div>
  <div class="foot-col" style="left:196px"><h5>Our Service</h5>Domestic<br>Industrial<br>Commercial<br>Heritage</div>
  <div class="foot-col" style="left:296px"><h5>Contact Us</h5>Seaview Victoria Australia<br>info@brightcoatpainting.com.au<br>1300 555 018
    <div class="social"><span></span><span></span><span></span></div></div>
  <div class="copyright">© 2014 Brightcoat Painting. All rights reserved. Terms apply.</div>
</footer>
</body>
</html>
```